Irrigation Business needs their business cards modernised and revamped

I would like to keep my current logo, colours and revamp the format of the card.

I would like the card to be clean yet important.

Im not sure if you include texture but i would like the named logo to be indented into the card etc.

show me something alive and free something thats clinical to the point yet has a feel of achievement. i would like people to go nice card.

Target Market(s)

high end clients, corporate, sports field manger, the guys that make the decisions

Industry/Entity Type

Business

Contact Information for Business Card

nformation to be included

Dean Harlow (Director)
0487305526
dean@kolvat.biz
www.kestonfieldworks.com

instagram logo
google logo
facebook logo

Colors

Designer to choose colors to be used in the design.

Requirements
Nice to have
• indentations a really nice feel to the card good texture

```html
<!DOCTYPE html>
<html lang="en">
<head>
<meta charset="utf-8">
<title>Keston Fieldworks – Business Card</title>
<link href="https://fonts.googleapis.com/css2?family=Roboto+Condensed:wght@400;700&family=Roboto:wght@400&display=swap" rel="stylesheet">
<style>
  :root {
    --bg: #2f2f2f;
    --card-front: #f1f1f1;
    --card-front-edge: #e4e4e4;
    --brand-blue: #2f68ad;
    --brand-sky: #36a6d8;
    --brand-green: #2e9b57;
    --text-grey: #555a60;
    --rule: #a9a9a9;
    --back-blue: #3d6fae;
    --back-blue-dark: #3566a5;
    --white: #ffffff;
  }
  * { margin: 0; padding: 0; box-sizing: border-box; }
  html, body { width: 1200px; height: 1166px; overflow: hidden; background: var(--bg); }
  .canvas { position: relative; width: 1200px; height: 1166px; }

  .card {
    position: absolute; left: 235px; width: 729px; height: 417px; overflow: hidden;
  }
  .card--front { top: 141px; background: linear-gradient(135deg, var(--card-front) 0%, var(--card-front-edge) 100%); }
  .card--back { top: 624px; background: linear-gradient(160deg, var(--back-blue) 0%, var(--back-blue-dark) 100%); }

  .decor { position: absolute; inset: 0; }

  .brand {
    position: absolute; display: flex; align-items: center; gap: 14px;
    font-family: "Roboto Condensed", sans-serif; font-weight: 700; letter-spacing: 0.5px;
  }
  .brand--front { right: 50px; top: 62px; flex-direction: column; gap: 14px; }
  .brand__dot { width: 98px; height: 98px; border-radius: 50%; background: var(--brand-sky); border: 5px solid var(--brand-blue); }
  .brand__name { font-size: 35px; color: var(--brand-blue); line-height: 1; }

  .person { position: absolute; left: 43px; top: 228px; font-family: "Roboto Condensed", sans-serif; }
  .person__name { font-size: 27px; font-weight: 700; color: var(--brand-blue); line-height: 1; }
  .person__role { font-size: 19px; font-weight: 400; color: var(--brand-green); margin-top: 10px; letter-spacing: 0.5px; }

  .rule { position: absolute; left: 43px; top: 290px; width: 643px; height: 1px; background: var(--rule); }

  .contacts { position: absolute; left: 43px; top: 304px; list-style: none; font-family: "Roboto", sans-serif; font-size: 17px; color: var(--text-grey); }
  .contacts li { display: flex; align-items: center; gap: 9px; height: 23px; }
  .contacts svg { width: 16px; height: 16px; fill: var(--brand-blue); }

  .brand--back { left: 34px; top: 285px; }
  .brand--back .brand__name { color: var(--white); font-size: 30px; }

  .social { position: absolute; left: 43px; top: 346px; display: flex; align-items: center; gap: 6px; }
  .social__line { width: 66px; height: 1px; background: rgba(255,255,255,0.6); }
  .social__icon { width: 36px; height: 36px; border-radius: 50%; background: var(--white); }
</style>
</head>
<body>
<main class="canvas">

  <section class="card card--front">
    <svg class="decor" viewBox="0 0 729 417" aria-hidden="true">
      <circle cx="168" cy="224" r="175" fill="#dbe4ea" opacity="0.55"/>
      <circle cx="168" cy="224" r="195" fill="none" stroke="#d9dfe5" stroke-width="10" opacity="0.8"/>
    </svg>

    <div class="brand brand--front">
      <span class="brand__dot"></span>
      <span class="brand__name">KESTON FIELDWORKS</span>
    </div>

    <div class="person">
      <h1 class="person__name">DEAN HARLOW</h1>
      <p class="person__role">DIRECTOR</p>
    </div>

    <div class="rule"></div>

    <ul class="contacts">
      <li>
        <svg viewBox="0 0 24 24" aria-hidden="true"><path d="M6.6 10.8a15.1 15.1 0 0 0 6.6 6.6l2.2-2.2a1 1 0 0 1 1-.25 11.4 11.4 0 0 0 3.6.57 1 1 0 0 1 1 1V20a1 1 0 0 1-1 1A17 17 0 0 1 3 4a1 1 0 0 1 1-1h3.5a1 1 0 0 1 1 1c0 1.25.2 2.45.57 3.57a1 1 0 0 1-.25 1z"/></svg>
        <span>0487305526</span>
      </li>
      <li>
        <svg viewBox="0 0 24 24" aria-hidden="true"><path d="M2 5h20v14H2z M3 6l9 7 9-7" fill="none" stroke="#2f68ad" stroke-width="2"/><path d="M2 5h20v3l-10 7L2 8z"/></svg>
        <span>dean@kolvat.biz</span>
      </li>
      <li>
        <svg viewBox="0 0 24 24" aria-hidden="true"><circle cx="12" cy="12" r="10"/><path d="M2 12h20M12 2c3 3 3 17 0 20M12 2c-3 3-3 17 0 20" fill="none" stroke="#f1f1f1" stroke-width="1.4"/></svg>
        <span>www.kestonfieldworks.com</span>
      </li>
    </ul>
  </section>

  <section class="card card--back">
    <svg class="decor" viewBox="0 0 729 417" aria-hidden="true">
      <circle cx="518" cy="214" r="200" fill="none" stroke="#ffffff" stroke-width="10" opacity="0.12"/>
      <circle cx="518" cy="214" r="178" fill="#ffffff" opacity="0.1"/>
    </svg>

    <div class="brand brand--back">
      <span class="brand__name">KESTON FIELDWORKS</span>
    </div>

    <div class="social" aria-label="Social media">
      <span class="social__line"></span>
      <span class="social__icon"></span>
      <span class="social__icon"></span>
      <span class="social__icon"></span>
      <span class="social__line"></span>
    </div>
  </section>

</main>
</body>
</html>
```